Redesign Digital Lending Mobile App - Android/ Flutter

Want to re-theme an existing Digital Lending Mobile app to simplify customer journeys, as well as uplift the UI.

Most users will have small screen phones so the design needs to take that into consideration while also adapting to those with larger devices, like admins with Tablets.

Have already laid out customer journeys on Figma with guidance on how the flow of the app should be. https://www.plankora.example/board/q4ZtRm81KdWe7YhXcvBnaL/LoomKit?frame-id=3-5182&s=Jk2pQwEr7TyUi-9

Video capture of current app: https://vaultbin.example/clip/7Hx3LmQp9RtZw2KcVn4YsBd8EfGj1/play
https://vaultbin.example/clip/4PsWq8ZnTk2LrXy6MbJc3VhGd9FeA/play

The documented views for Web are also here https://docshelf.example/open?ref=3B8F2204AD7C91E5!tk8d1f6a2c4e7b90d3f5a1c8e2b6d4f9a07&cid=3b8f2204ad7c91e5&kind=file%2Cdocx&wdo=2

Target Market(s)

Kenya, Tanzania, Uganda - Africa

Industry/Entity Type

Fintech

Requirements
Must have
• Responsive for diff screens, esp. in context of smaller screen smartphone
Nice to have
• Thematic components to ensure new views can easily be adapted to these themse

```html
<!DOCTYPE html>
<html lang="en">
<head>
<meta charset="utf-8">
<title>LoomKit – Lending App Screens</title>
<link href="https://fonts.googleapis.com/css2?family=Montserrat:wght@400;500;600;700;800&display=swap" rel="stylesheet">
<style>
:root{
  --page:#f2f2f2;
  --blue:#3776c6;
  --blue-text:#2f6fc2;
  --navy:#0b3f8a;
  --sky-top:#f7fcff;
  --sky-bottom:#dcf1fc;
  --ink:#1b1b1b;
  --muted:#8a8a8a;
  --line:#d5dbe2;
  --red:#e0302a;
  --kb:#151515;
  --key:#3b3b3b;
  --key-dark:#262626;
  --scene-light:#7fbcef;
  --scene-dark:#0d4a9c;
}
*{box-sizing:border-box;margin:0;padding:0}
html,body{width:961px;height:1200px;overflow:hidden}
body{background:var(--page);font-family:"Montserrat",sans-serif;color:var(--ink);position:relative}
.screen{position:absolute;width:208px;height:455px;border-radius:16px;overflow:hidden;
  background:linear-gradient(180deg,var(--sky-top),var(--sky-bottom))}
.abs{position:absolute}
.scene-placeholder{position:absolute;left:0;right:0;
  background:linear-gradient(180deg,var(--scene-light) 0%,var(--scene-dark) 100%)}
.btn{position:absolute;left:14px;width:179px;height:23px;border-radius:3px;background:var(--blue);
  color:#fff;font-size:8px;display:flex;align-items:center;justify-content:center}
.label{position:absolute;left:14px;font-size:6.5px;font-weight:500}
.input{position:absolute;left:14px;width:179px;height:24px;background:#fff;border:1px solid var(--line);
  border-radius:3px;font-size:6px;color:#aaa;padding-left:10px;display:flex;align-items:center}
.link{color:var(--blue-text)}
/* splash */
.brand{position:absolute;left:0;right:0;top:200px;display:flex;flex-direction:column;align-items:center;gap:8px}
.brand-dot{width:40px;height:40px;border-radius:50%;background:var(--blue)}
.brand-name{font-size:20px;font-weight:800;color:var(--blue)}
.version{position:absolute;left:0;right:0;text-align:center;font-size:7px}
/* pin */
.pin-title{position:absolute;left:0;right:0;top:76px;text-align:center;font-size:8px;font-weight:500}
.pin-row{position:absolute;left:14px;top:93px;width:179px;display:flex;justify-content:space-between}
.pin-box{width:22px;height:24px;border:1px solid #bbb;border-radius:3px;background:#fff;font-size:17px;display:flex;align-items:center;justify-content:center}
.keyboard{position:absolute;left:0;right:0;top:280px;bottom:0;background:var(--kb);color:#eee}
.chip{position:absolute;left:75px;top:5px;width:58px;height:17px;border-radius:9px;background:#3a3a3a;font-size:7px;color:#ccc;display:flex;align-items:center;justify-content:center}
.krow{position:absolute;left:3px;right:3px;display:flex;justify-content:center;gap:2.5px}
.key{width:17.5px;height:25px;border-radius:4px;background:var(--key);font-size:11px;display:flex;align-items:center;justify-content:center}
.key.fn{background:var(--key-dark);width:26px;font-size:8px}
.key.space{width:80px;font-size:7px;color:#ddd}
/* home */
.greet{position:absolute;left:14px;top:16px;font-size:11px;font-weight:700}
.greet-sub{position:absolute;left:14px;top:31px;font-size:7px;color:#444}
.avatar-sm{position:absolute;left:168px;top:15px;width:26px;height:26px;border-radius:50%;background:#5b6a86;border:2px solid #222}
.avatar-sm .badge{position:absolute;right:-4px;bottom:-5px;width:13px;height:13px;border-radius:50%;background:var(--blue);border:1px solid #fff}
.section-head{position:absolute;left:14px;right:15px;top:172px;display:flex;justify-content:space-between;align-items:center;font-size:6.5px;font-weight:700}
.section-head .link{font-size:5.5px;font-weight:500}
.plan{position:absolute;left:14px;width:179px;height:87px;background:#fff;border:1px solid var(--line);border-radius:6px}
.plan-tag{position:absolute;top:4px;height:12px;padding:0 7px;border-radius:7px;background:#f1f1f1;border:1px solid #ddd;font-size:5px;display:flex;align-items:center}
.plan-tag.bad{left:4px;color:var(--red)}
.plan-tag.cap{right:4px}
.plan-name{position:absolute;left:56px;top:-5px;width:66px;height:19px;border-radius:10px;background:var(--blue);color:#fff;font-size:7px;display:flex;align-items:center;justify-content:center;box-shadow:0 0 0 3px #fff}
.plan-body{position:absolute;left:7px;right:7px;top:28px;font-size:5.3px;line-height:1.3;color:#777}
.tabbar{position:absolute;left:14px;top:410px;width:179px;height:30px;background:#fff;border:1px solid var(--line);border-radius:5px;display:flex;align-items:center;justify-content:space-around;padding:0 3px}
.tab{font-size:6.5px;font-weight:600;display:flex;flex-direction:column;align-items:center;gap:1px}
.tab.active{flex-direction:row;gap:4px;background:var(--blue);color:#fff;width:62px;height:22px;border-radius:3px;justify-content:center;font-weight:500}
/* drawer */
.drawer{position:absolute;left:0;top:0;bottom:0;width:157px;background:var(--blue);color:#fff}
.avatar-lg{position:absolute;left:48px;top:24px;width:60px;height:60px;border-radius:50%;background:#56657f;border:3px solid #111}
.level{position:absolute;left:72px;top:65px;width:36px;height:36px;border-radius:50%;background:#fff;color:var(--blue-text);font-size:6.5px;font-weight:700;display:flex;align-items:center;justify-content:center}
.who{position:absolute;left:0;right:0;top:109px;text-align:center}
.who b{display:block;font-size:10px;font-weight:700}
.who span{display:block;font-size:6.3px;line-height:1.2}
.rule{position:absolute;left:14px;width:127px;height:1px;background:#fff}
.menu-item{position:absolute;left:14px;font-size:8px;font-weight:500;display:flex;align-items:center;gap:5px}
.menu-item svg{width:10px;height:10px}
</style>
</head>
<body>

<!-- Splash -->
<section class="screen" style="left:105px;top:110px">
  <div class="brand"><div class="brand-dot"></div><div class="brand-name">LoomKit</div></div>
  <div class="version" style="top:435px">Version 1.0</div>
</section>

<!-- Log in -->
<section class="screen" style="left:376px;top:110px">
  <div class="abs" style="left:14px;top:76px;font-size:17px;font-weight:700;color:var(--blue-text)">Log In</div>
  <div class="label" style="top:127px">UserName or Email:</div>
  <div class="input" style="top:140px">Enter UserName or Email</div>
  <div class="label" style="top:168px">Password:</div>
  <div class="input" style="top:180px">Enter Password</div>
  <div class="label link" style="top:209px">Forgot Password?</div>
  <div class="btn" style="top:221px">Login</div>
  <div class="abs" style="left:14px;width:179px;top:249px;display:flex;align-items:center;gap:4px;font-size:7px">
    <span style="flex:1;height:1px;background:#777"></span>or<span style="flex:1;height:1px;background:#777"></span>
  </div>
  <div class="btn" style="top:261px;background:#fff;color:#333;font-weight:500">Gleamly</div>
  <div class="label" style="top:291px">Not have account: <span class="link">Register Now</span></div>
  <div class="abs" style="left:14px;top:313px;width:11px;height:11px;border:1px solid #bbb;border-radius:2px;background:#fff"></div>
  <div class="abs" style="left:28px;top:311px;width:168px;font-size:6.5px;line-height:1.25;font-weight:500">I'm agree to the <span class="link">Term of Service</span> and the <span class="link">Privacy Policy.</span></div>
  <div class="scene-placeholder" role="img" aria-label="City skyline illustration in blue tones" style="top:359px;bottom:0"></div>
</section>

<!-- PIN -->
<section class="screen" style="left:647px;top:110px">
  <div class="pin-title">Enter Your Pin</div>
  <div class="pin-row">
    <div class="pin-box">7</div><div class="pin-box">9</div><div class="pin-box">7</div>
    <div class="pin-box">0</div><div class="pin-box">9</div><div class="pin-box">3</div>
  </div>
  <div class="btn" style="top:127px">Submit</div>
  <div class="scene-placeholder" role="img" aria-label="City skyline illustration in blue tones" style="top:182px;height:98px"></div>
  <div class="keyboard">
    <div class="chip">797093</div>
    <div class="krow" style="top:29px"><div class="key">q</div><div class="key">w</div><div class="key">e</div><div class="key">r</div><div class="key">t</div><div class="key">y</div><div class="key">u</div><div class="key">i</div><div class="key">o</div><div class="key">p</div></div>
    <div class="krow" style="top:60px"><div class="key">a</div><div class="key">s</div><div class="key">d</div><div class="key">f</div><div class="key">g</div><div class="key">h</div><div class="key">j</div><div class="key">k</div><div class="key">l</div></div>
    <div class="krow" style="top:91px"><div class="key fn">⇧</div><div class="key">z</div><div class="key">x</div><div class="key">c</div><div class="key">v</div><div class="key">b</div><div class="key">n</div><div class="key">m</div><div class="key fn">⌫</div></div>
    <div class="krow" style="top:122px"><div class="key fn">?123</div><div class="key fn" style="width:20px">☺</div><div class="key fn" style="width:18px">,</div><div class="key space">English (USA)</div><div class="key fn" style="width:18px">.</div><div class="key fn" style="color:#4a90e2">⌕</div></div>
    <div class="abs" style="left:17px;top:158px;font-size:8px;color:#ccc">⌄</div>
  </div>
</section>

<!-- Home -->
<section class="screen" style="left:105px;top:630px">
  <div class="greet">Good Morning</div>
  <div class="greet-sub">John Doe</div>
  <div class="avatar-sm" role="img" aria-label="User avatar placeholder"><span class="badge"></span></div>
  <div class="scene-placeholder" role="img" aria-label="City skyline illustration in blue tones" style="top:60px;height:99px"></div>
  <div class="section-head"><span>Loan Eligibility Plans</span><span class="link">View all plans</span></div>

  <article class="plan" style="top:200px">
    <span class="plan-tag bad">Not Eligible</span><span class="plan-name">Plan 1</span><span class="plan-tag cap">Upto $10000</span>
    <p class="plan-body">Lorem ipsum dolor sit amet, consectetuer adipiscing elit, sed diam nonummy nibh euismod tincidunt ut laoreet dolore magna aliquam erat volutpat. Ut wisi enim ad minim veniam, quis nostrud exerci tation ullamcorper suscipit lobortis nisl ut aliquip ex ea commodo consequat. Duis autem vel eum iriure dolor in hendrerit in vulputate velit esse molestie <span class="link">read more</span></p>
  </article>
  <article class="plan" style="top:308px">
    <span class="plan-tag bad">Not Eligible</span><span class="plan-name">Plan 2</span><span class="plan-tag cap">Upto $10000</span>
    <p class="plan-body">Lorem ipsum dolor sit amet, consectetuer adipiscing elit, sed diam nonummy nibh euismod tincidunt ut laoreet dolore magna aliquam erat volutpat. Ut wisi enim ad minim veniam, quis nostrud exerci tation ullamcorper suscipit lobortis nisl ut aliquip ex ea commodo consequat. Duis autem vel eum iriure dolor in hendrerit in vulputate velit esse molestie <span class="link">read more</span></p>
  </article>

  <nav class="tabbar">
    <span class="tab active"><svg width="10" height="10" viewBox="0 0 10 10" fill="none" stroke="#fff" stroke-width="0.9"><path d="M1 9V4.5L5 1l4 3.5V9z"/></svg>Home</span>
    <span class="tab"><svg width="9" height="10" viewBox="0 0 9 10" fill="none" stroke="#222" stroke-width="0.9"><path d="M4.5 9.5C2 9.5 1 8 1 6.3 1 4 3.5 3 4 .5c1.5 1.5 4 3.5 4 5.8 0 1.7-1 3.2-3.5 3.2z"/></svg>Tutorials</span>
    <span class="tab"><svg width="10" height="10" viewBox="0 0 10 10" fill="none" stroke="#222" stroke-width="0.9"><circle cx="5" cy="5" r="1.6"/><circle cx="5" cy="5" r="3.8" stroke-dasharray="2 1"/></svg>Setting</span>
  </nav>
</section>

<!-- Drawer -->
<section class="screen" style="left:376px;top:630px">
  <div class="scene-placeholder" role="img" aria-label="City skyline illustration in blue tones" style="top:391px;bottom:0;left:150px"></div>
  <aside class="drawer">
    <div class="avatar-lg" role="img" aria-label="User avatar placeholder"></div>
    <div class="level">Level: 2</div>
    <div class="who"><b>John Doe</b><span>Branch</span><span>Organization</span></div>
    <div class="rule" style="top:143px"></div>
    <div class="menu-item" style="top:160px"><svg viewBox="0 0 10 10" fill="none" stroke="#fff" stroke-width="0.8"><rect x=".5" y=".5" width="4" height="5"/><rect x="5.5" y=".5" width="4" height="3"/><rect x=".5" y="6.5" width="4" height="3"/><rect x="5.5" y="4.5" width="4" height="5"/></svg>Dashboard</div>
    <div class="menu-item" style="top:199px"><svg viewBox="0 0 10 10" fill="none" stroke="#fff" stroke-width="0.8"><circle cx="5" cy="3" r="2.2"/><path d="M1 9.5c0-2.5 2-4 4-4s4 1.5 4 4z"/></svg>Clients</div>
    <div class="menu-item" style="top:238px"><svg viewBox="0 0 10 10" fill="none" stroke="#fff" stroke-width="0.7"><circle cx="5" cy="3.5" r="1.5"/><circle cx="2" cy="4.5" r="1.1"/><circle cx="8" cy="4.5" r="1.1"/><path d="M2.5 8.5c0-1.7 1.2-2.6 2.5-2.6s2.5.9 2.5 2.6zM.3 8.5c0-1.3.8-2 1.7-2M9.7 8.5c0-1.3-.8-2-1.7-2"/></svg>Groups</div>
    <div class="menu-item" style="top:277px"><svg viewBox="0 0 10 10" fill="none" stroke="#fff" stroke-width="0.7"><rect x=".5" y="2" width="6" height="7.5"/><rect x="6.5" y="4" width="3" height="5.5"/><path d="M2 4h1M4 4h1M2 6h1M4 6h1"/></svg>Centers</div>
    <div class="menu-item" style="top:316px"><svg viewBox="0 0 10 10" fill="none" stroke="#fff" stroke-width="0.8"><circle cx="5" cy="5" r="4.5"/><circle cx="5" cy="4" r="1.6"/><path d="M2.2 8.3c.6-1.3 1.6-2 2.8-2s2.2.7 2.8 2"/></svg>Profile</div>
    <div class="abs" style="right:16px;top:411px;font-size:8px;font-weight:500">Version 1.0</div>
    <div class="rule" style="top:425px"></div>
    <div class="menu-item" style="top:432px;gap:14px"><svg viewBox="0 0 10 10" fill="none" stroke="#fff" stroke-width="0.8"><path d="M4 .5H.5v9H4M3.5 5h6M7.5 3l2 2-2 2"/></svg>Log out</div>
  </aside>
</section>

</body>
</html>
```